Brightway Haus Inc. Business Card Design

Brightway Haus Inc. is in search of a great clean design for our business cards!

Looking to incorporate our full logo and watermark on side one (however, I am open to having the text and watermark separated within the design.)

On side two, I am looking to have contact information (Name, Position, Phone #, Email, Website (www.thebrightwayhaus.ca). Can have the logo and/or watermark as part of the design if applicable.

Please add tagline "Where Shine Counts" on either side 1 or 2. This tagline can be in a sans serif, serif or cursive font as long as it compliments overall design. Capitalization can be title or sentence case depending on how it fits within the design.

Get creative!! Looking for a clean, crisp, premium design! Looking for a glossy card finish with spot UV features when printed. Cards will also be printed with rounded corners. Standard dimensions (3.5 x 2).

Target Market(s)

B2B - primary clients are business owners or property management corporations. (residential jobs are few and far between)

Industry/Entity Type

Business

Contact Information for Business Card

- clean, crisp design
- double sided
- spot UV accents and glossy finish upon printing
- standard business card size (3.5 x 2) with rounded corners
- please see project description for requirements per side

Font styles to use
Sans Serif

Requirements
Must have
• - adequate bleeds with print ready files
• - cohesive design elements between side 1 & 2
• - spot UV elements (can be on both sides or just one, use your discretion)
• - colour pallet should match the logo file provided
• - incorporate tagline "where shine counts" (this tagline can be in a serif or sans serif font as long as it is complimentary to the overall design.
Nice to have
• - Premium elements with a clean design
Should not have
• - Please omit cartoon or whimsical like designs, think premium.
• - Colours should not stray from the pallet of the provided logo.

```html
<!DOCTYPE html>
<html lang="en">
<head>
<meta charset="UTF-8">
<title>Brightway Haus Inc. — Business Card</title>
<link rel="stylesheet" href="https://fonts.googleapis.com/css2?family=Open+Sans:wght@700&family=Roboto:wght@400;500&family=Roboto+Condensed:wght@500&display=swap">
<style>
  :root {
    --backdrop: #e9e6e1;
    --card-dark: #1d1f21;
    --card-light: #f4f4f4;
    --teal: #17b3b8;
    --navy: #1c2752;
    --grey-text: #555a60;
    --white: #ffffff;
    --mark-tint: rgba(23, 179, 184, 0.12);
  }
  * { margin: 0; padding: 0; box-sizing: border-box; }
  html, body { width: 1200px; height: 960px; overflow: hidden; }
  body { background: var(--backdrop); position: relative; font-family: "Roboto", Arial, sans-serif; }

  .card { position: absolute; overflow: hidden; box-shadow: 0 2px 6px rgba(0,0,0,0.25); }

  /* Side one */
  .card-front {
    left: 322px; top: 108px; width: 606px; height: 344px;
    border-radius: 22px; background: var(--card-dark);
  }
  .card-front .watermark {
    position: absolute; left: 448px; top: 130px; width: 348px; height: 296px;
    background: var(--mark-tint); border-radius: 4px;
    left: 126px; top: 22px;
  }
  .card-front .brand-name {
    position: absolute; left: 0; right: 0; top: 128px; text-align: center;
    font-family: "Open Sans", Arial, sans-serif; font-weight: 700;
    font-size: 40px; letter-spacing: -0.5px; color: var(--teal); line-height: 1;
  }
  .card-front .tagline {
    position: absolute; left: 0; right: 0; top: 194px; text-align: center;
    font-size: 15px; letter-spacing: 8px; color: var(--white);
  }

  /* Side two */
  .card-back {
    left: 320px; top: 493px; width: 600px; height: 342px;
    border-radius: 18px; background: var(--card-light);
  }
  .card-back .brand-name {
    position: absolute; right: 34px; top: 38px;
    font-family: "Open Sans", Arial, sans-serif; font-weight: 700;
    font-size: 28px; letter-spacing: -0.3px; color: var(--teal); line-height: 1;
  }
  .contact { position: absolute; left: 28px; top: 118px; }
  .contact .person-name {
    font-family: "Roboto Condensed", Arial, sans-serif; font-weight: 500;
    font-size: 21px; color: var(--teal); line-height: 1.2;
  }
  .contact .person-role { font-weight: 500; font-size: 15px; color: var(--navy); margin-top: 4px; }
  .contact .address { font-size: 14.5px; color: var(--grey-text); line-height: 18px; margin-top: 12px; }
  .contact .lines { list-style: none; margin-top: 12px; }
  .contact .lines li {
    display: flex; align-items: center; gap: 8px;
    font-size: 14.5px; color: var(--grey-text); line-height: 19px;
  }
  .contact .lines svg { width: 14px; height: 14px; fill: var(--teal); flex: none; }
</style>
</head>
<body>

<section class="card card-front" aria-label="Card side one">
  <div class="watermark"></div>
  <div class="brand-name">BRIGHTWAY HAUS INC.</div>
  <div class="tagline">Where Shine Counts</div>
</section>

<section class="card card-back" aria-label="Card side two">
  <div class="brand-name">BRIGHTWAY HAUS INC.</div>
  <div class="contact">
    <div class="person-name">MARA LINDQVIST</div>
    <div class="person-role">CEO/FOUNDER</div>
    <div class="address">2190 Harbourview Court<br>Halifax, Nova Scotia B3K 2L4</div>
    <ul class="lines">
      <li>
        <svg viewBox="0 0 16 16" aria-hidden="true"><path d="M3.5 1.5l2.5 0.3 1 3-1.6 1.3a9 9 0 0 0 4.5 4.5l1.3-1.6 3 1 .3 2.5-1.8 1.8C7 14 2 9 1.7 3.3z"/></svg>
        902 555 0148
      </li>
      <li>
        <svg viewBox="0 0 16 16" aria-hidden="true"><path d="M4.5 1h7a1 1 0 0 1 1 1v12a1 1 0 0 1-1 1h-7a1 1 0 0 1-1-1V2a1 1 0 0 1 1-1zm.8 2v8.5h5.4V3zM8 12.3a.8.8 0 1 0 0 1.6.8.8 0 0 0 0-1.6z"/></svg>
        902 555 0173
      </li>
      <li>
        <svg viewBox="0 0 16 16" aria-hidden="true"><path d="M4 1h8v4H4zM1.5 6h13a1 1 0 0 1 1 1v5h-3v3h-9v-3h-3V7a1 1 0 0 1 1-1zm3.5 5v2.5h6V11z"/></svg>
        902 555 0196
      </li>
      <li>
        <svg viewBox="0 0 16 16" aria-hidden="true"><path d="M1 3.5h14v1L8 9 1 4.5zM1 6l7 4.5L15 6v6.5H1z"/></svg>
        hello@thebrightwayhaus.ca
      </li>
      <li>
        <svg viewBox="0 0 16 16" aria-hidden="true"><path d="M8 1a7 7 0 1 0 0 14A7 7 0 0 0 8 1zm0 1.6c.8 0 1.8 1.6 2.1 4.2H5.9C6.2 4.2 7.2 2.6 8 2.6zM2.7 8.8h2.2c.1 1.8.5 3.2 1 4.1a5.5 5.5 0 0 1-3.2-4.1zm0-1.6a5.5 5.5 0 0 1 3.2-4.1c-.5.9-.9 2.3-1 4.1zm5.3 6.2c-.8 0-1.8-1.6-2.1-4.6h4.2c-.3 3-1.3 4.6-2.1 4.6zm2.1-.5c.5-.9.9-2.3 1-4.1h2.2a5.5 5.5 0 0 1-3.2 4.1zm1-5.7c-.1-1.8-.5-3.2-1-4.1a5.5 5.5 0 0 1 3.2 4.1z"/></svg>
        www.thebrightwayhaus.ca
      </li>
    </ul>
  </div>
</section>

</body>
</html>
```